Belmont Ridge Business Card Design Project

We have recently rebranded and would like to design new business cards that incorporate the corporate logo - double sided cards with corporate logo on one side and contact details on the other

Target Market(s)

Sophisticated and high net worth investors and finance industry professionals

Industry/Entity Type

Funds Management

Contact Information for Business Card

The card should prominently feature the company name and logo. Other details will be standard contact details for each staff member - name, address, phone, email, website

Colors
0054AA
0677BA
7BADD7
CADEEF
E8F1F8

Requirements
Must have
• Double-sided design with one side prominently featuring the corporate logo and the other side with all standard contact details

```html
<!DOCTYPE html>
<html lang="en">
<head>
<meta charset="utf-8">
<title>Belmont Ridge — Business Cards</title>
<link rel="stylesheet" href="https://fonts.googleapis.com/css2?family=Cinzel:wght@500&family=Arimo:wght@400;700&display=swap">
<style>
  :root {
    --backdrop: #e8e8e6;
    --card-navy: #21467a;
    --card-navy-deep: #1b3b69;
    --pattern-light: #3f6fb0;
    --ink-light: #ffffff;
    --ink-soft: #dfe8f3;
    --rule: rgba(255,255,255,0.75);
  }
  * { box-sizing: border-box; margin: 0; padding: 0; }
  html, body { width: 1200px; height: 802px; overflow: hidden; }
  body {
    background: var(--backdrop);
    display: flex;
    align-items: center;
    justify-content: center;
    gap: 56px;
  }
  .card {
    position: relative;
    width: 525px;
    height: 300px;
    border-radius: 3px;
    background: var(--card-navy);
    color: var(--ink-light);
    overflow: hidden;
    box-shadow: 0 10px 24px rgba(0,0,0,0.18);
  }
  .wordmark {
    font-family: "Cinzel", serif;
    font-weight: 500;
    color: var(--ink-light);
    letter-spacing: 1px;
    white-space: nowrap;
  }

  /* Front: contact side */
  .card-front .wordmark {
    position: absolute;
    top: 64px;
    left: 0;
    right: 0;
    text-align: center;
    font-size: 30px;
  }
  .front-details {
    position: absolute;
    top: 138px;
    left: 58px;
    right: 40px;
    display: flex;
    align-items: center;
  }
  .staff {
    width: 175px;
    text-align: right;
    padding-right: 18px;
    font-family: "Arimo", sans-serif;
  }
  .staff-name { font-weight: 700; font-size: 17px; letter-spacing: 0.3px; }
  .staff-role { font-size: 13px; color: var(--ink-soft); margin-top: 3px; }
  .divider { width: 1px; height: 64px; background: var(--rule); }
  .contact-list {
    list-style: none;
    padding-left: 18px;
    font-family: "Arimo", sans-serif;
    font-size: 13.5px;
    line-height: 21px;
  }
  .contact-list li { display: flex; align-items: center; gap: 8px; }
  .contact-list svg { width: 12px; height: 12px; fill: var(--ink-light); flex: none; }
  .address {
    position: absolute;
    bottom: 46px;
    left: 0;
    right: 0;
    text-align: center;
    font-family: "Arimo", sans-serif;
    font-size: 13.5px;
    color: var(--ink-soft);
  }

  /* Back: brand side */
  .card-back { background: var(--card-navy-deep); }
  .brand-pattern {
    position: absolute;
    inset: 0;
    background:
      radial-gradient(ellipse at 85% 35%, rgba(79,131,200,0.65), transparent 55%),
      linear-gradient(120deg, var(--card-navy-deep) 0%, var(--card-navy) 55%, var(--pattern-light) 100%);
  }
  .card-back .wordmark {
    position: absolute;
    top: 50%;
    left: 0;
    right: 0;
    transform: translateY(-50%);
    text-align: center;
    font-size: 36px;
  }
</style>
</head>
<body>
  <section class="card card-front" aria-label="Business card, contact side">
    <div class="wordmark">Belmont Ridge</div>
    <div class="front-details">
      <div class="staff">
        <div class="staff-name">DANIEL HARPER</div>
        <div class="staff-role">Manager</div>
      </div>
      <div class="divider"></div>
      <ul class="contact-list">
        <li>
          <svg viewBox="0 0 24 24" aria-hidden="true"><path d="M6.6 10.8a15 15 0 0 0 6.6 6.6l2.2-2.2c.3-.3.7-.4 1-.2 1.1.4 2.3.6 3.6.6.6 0 1 .4 1 1V20c0 .6-.4 1-1 1A17 17 0 0 1 3 4c0-.6.4-1 1-1h3.5c.6 0 1 .4 1 1 0 1.3.2 2.5.6 3.6.1.3 0 .7-.2 1z"/></svg>
          555-014-2100
        </li>
        <li>
          <svg viewBox="0 0 24 24" aria-hidden="true"><path d="M2 5h20v14H2zm2 2v.5l8 5 8-5V7l-8 5z"/></svg>
          contact@belmontridge.com
        </li>
        <li>
          <svg viewBox="0 0 24 24" aria-hidden="true"><circle cx="12" cy="12" r="10"/></svg>
          www.belmontridge.com
        </li>
      </ul>
    </div>
    <div class="address">Your Address, City, State, Zip 0000</div>
  </section>

  <section class="card card-back" aria-label="Business card, brand side">
    <div class="brand-pattern" role="img" aria-label="Embossed repeating brand-symbol pattern in navy and light blue"></div>
    <div class="wordmark">Belmont Ridge</div>
  </section>
</body>
</html>
```